Exclusive British Dental Clinic Needs Modern Brochure to Attract New Patients

We are looking to create a smart, sophisticated brochure that gives the public and future potential clients a concise overview of what we offer and why the quality and care on offer is a step above the rest. We are based in the United Kingdom where the Corbridge Welfare Board provide dental care free or at low cost. We are NOT an CWB provider. We are a wholly private dental clinic so all of our patients are paying full-price premium prices directly out of pocket. The work we do is exceptional so all of our patients can be assured that anything we do is done to the highest and best quality possible.
We offer high quality dental treatment using the best and latest techniques, materials and an award winning dental laboratory. All treatments are undertaken using high quality magnification to ensure the best possible result. We have over 30 years’ experience in general dentistry with fully trained staff. In quality comfortable surroundings, we are a caring practice with excellent patient care. We allow more time with our patients and we understand and care for nervous patients.
We also offer facial fillers, wrinkle reducers and teeth whitening in order to help our patients achieve their best look.

We have attached our logo and logo icons to this brief.
We also have attached some information in our Brochure Details document. This just highlights what we would like to see and more information about us.
We are really up to suggestion with design and wording because we want this brochure to be attractive and appealing to the public.
Feel free to edit as you see fit to help us attain our goals :)

Reason: Hello We are very excited about the work we have received thus far...our Practice Manager is away for the next week and we wanted to make sure we are all on board for the discussions and decisions we make moving forward. Thank you for taking the time to help us create our voice! --- Larkmoor Fenwick Dental Clinic

```html
<!DOCTYPE html>
<html lang="en">
<head>
<meta charset="utf-8">
<title>Larkmoor Fenwick Dental Clinic – Brochure</title>
<link href="https://fonts.googleapis.com/css2?family=Montserrat:wght@400;600&family=Open+Sans:wght@300;400&display=swap" rel="stylesheet">
<style>
  :root {
    --backdrop: #e9e5e2;
    --paper: #ffffff;
    --brand-blue: #6f9fd4;
    --brand-navy: #2e3a52;
    --ink: #4a4f57;
    --dots: #9cbbe0;
    --photo-light: #f5f1ee;
    --photo-warm: #dcc1ab;
    --photo-tan: #c39a7c;
    --photo-cool: #b9c8d6;
  }
  * { box-sizing: border-box; margin: 0; padding: 0; }
  html, body { width: 1200px; height: 900px; overflow: hidden; }
  body {
    background: var(--backdrop);
    font-family: "Open Sans", Arial, sans-serif;
    color: var(--ink);
    position: relative;
  }
  .panel {
    position: absolute;
    top: 110px;
    width: 330px;
    height: 680px;
    background: var(--paper);
    box-shadow: 0 6px 24px rgba(0,0,0,0.08);
  }
  .panel--back { left: 240px; }
  .panel--front { left: 630px; }

  /* back panel */
  .web-address {
    position: absolute;
    top: 250px; left: 0; right: 0;
    display: flex; justify-content: center; align-items: center; gap: 8px;
    font-family: "Montserrat", Arial, sans-serif;
    font-size: 13px; letter-spacing: 2.4px;
    color: var(--brand-blue);
  }
  .dot-icon {
    width: 11px; height: 11px;
    border: 1px solid var(--brand-blue);
    border-radius: 50%;
    flex: none;
  }
  .contact {
    position: absolute;
    left: 24px; right: 24px; bottom: 22px;
    text-align: center;
  }
  .contact__name {
    font-family: "Montserrat", Arial, sans-serif;
    font-weight: 600; font-size: 9.5px;
    color: var(--brand-blue);
    letter-spacing: 0.4px;
    text-transform: uppercase;
  }
  .contact__address { font-size: 8.5px; line-height: 1.35; color: var(--ink); }
  .contact__lines {
    display: flex; justify-content: space-between;
    font-size: 8.5px; margin-top: 6px; padding: 0 6px;
  }
  .contact__lines b { color: var(--brand-blue); font-weight: 600; margin-right: 3px; }
  .social {
    margin-top: 6px;
    border-top: 1.5px dotted var(--dots);
  }
  .social__row {
    display: flex; justify-content: center; align-items: center; gap: 8px;
    padding: 5px 0;
    font-size: 11.5px; letter-spacing: 0.8px;
    color: var(--brand-blue);
    border-bottom: 1.5px dotted var(--dots);
  }

  /* front cover */
  .headline {
    position: absolute;
    top: 130px; left: 0; right: 0;
    text-align: center;
    font-weight: 300; font-size: 21px;
    color: var(--ink);
    letter-spacing: 0.5px;
  }
  .headline__smile { color: var(--brand-blue); font-size: 26px; margin-left: 10px; }
  .cover-photo {
    position: absolute;
    top: 205px; left: 0; right: 0;
    height: 405px;
    background: linear-gradient(115deg,
      var(--photo-light) 0%,
      var(--photo-warm) 38%,
      var(--photo-tan) 62%,
      var(--photo-cool) 100%);
  }
  .brand-lockup {
    position: absolute;
    left: 0; right: 0; bottom: 22px;
    display: flex; justify-content: center; align-items: center; gap: 10px;
  }
  .brand-lockup__mark {
    width: 34px; height: 34px;
    border: 1.5px solid var(--brand-blue);
    border-radius: 50%;
  }
  .brand-lockup__name {
    font-family: "Montserrat", Arial, sans-serif;
    font-weight: 400; font-size: 13px;
    line-height: 1.3; letter-spacing: 0.8px;
    color: var(--brand-navy);
    text-transform: uppercase;
  }
</style>
</head>
<body>
  <section class="panel panel--back" aria-label="Back panel">
    <p class="web-address"><span class="dot-icon"></span>www.larkmoorfenwick.com</p>
    <div class="contact">
      <p class="contact__name">Larkmoor Fenwick Dental Clinic</p>
      <p class="contact__address">14 Orchard Row, Hallowmere,<br>Westshire, HW3 8QT.</p>
      <p class="contact__lines">
        <span><b>T</b>01632 960 417</span>
        <span><b>E</b>enquiries@larkmoorfenwick.com</span>
      </p>
      <div class="social">
        <p class="social__row"><span class="dot-icon"></span>chatterbook.net/LarkmoorFenwick</p>
        <p class="social__row"><span class="dot-icon"></span>tweetline.net/Larkmoor_Dental</p>
      </div>
    </div>
  </section>

  <section class="panel panel--front" aria-label="Front cover">
    <h1 class="headline">Freedom to<span class="headline__smile">:)</span></h1>
    <div class="cover-photo" role="img" aria-label="Photograph of a smiling woman with long brown hair resting her head on her hand"></div>
    <div class="brand-lockup">
      <span class="brand-lockup__mark"></span>
      <p class="brand-lockup__name">Larkmoor Fenwick<br>Dental Clinic</p>
    </div>
  </section>
</body>
</html>
```